Business Card Design 2018 Kestrel Machining

Hello,

We need a business card design to reflect our new website we just had designed ( http://www.kestrelmachining.ca/)

We are a growing machine shop looking to grow our clientele and are hoping to update our current business card design to match our website and industry

The colours and design of our website should match to achieve what we are looking for.

I have attached a few images for reference as well as our logo and ISO 9000 needs to be apparent on the card as well

Please let me know what you have :)
Please copy marla@kestrelmachining.ca on all communication regarding this project

Thanks !!!

Industry/Entity Type

Business

Contact Information for Business Card

Company Name, employee name and title and contact details

Colors
f78f20
ffffff
00a990

Requirements
Must have
• Our logo, Iso 9000 same colours as our website http://www.kestrelmachining.ca/

```html
<!DOCTYPE html>
<html lang="en">
<head>
<meta charset="utf-8">
<title>Kestrel Machining – Business Card</title>
<link rel="stylesheet" href="https://fonts.googleapis.com/css2?family=Roboto:wght@400;700;900&family=Roboto+Condensed:wght@400;700&display=swap">
<style>
  :root {
    --canvas-bg: #e9e7e4;
    --card-white: #f4f4f4;
    --card-black: #000000;
    --teal: #1a9ea3;
    --teal-light: #3cc3c7;
    --ink: #111111;
    --grey-text: #555555;
    --divider: #c9c9c9;
  }
  * { margin: 0; padding: 0; box-sizing: border-box; }
  html, body { width: 1200px; height: 960px; overflow: hidden; }
  body {
    position: relative;
    background: var(--canvas-bg);
    font-family: "Roboto", Arial, sans-serif;
  }
  .card {
    position: absolute;
    width: 600px;
    height: 343px;
    overflow: hidden;
  }
  .brand {
    position: absolute;
    display: flex; align-items: center;
    white-space: nowrap;
  }
  .brand-name {
    font-family: "Roboto", Arial, sans-serif;
    font-weight: 900; text-transform: uppercase; line-height: 1;
  }

  /* Front */
  .card-front { left: 314px; top: 113px; background: var(--card-white); }
  .card-front .brand { left: 65px; top: 143px; width: 250px; gap: 8px; }
  .card-front .brand-square { width: 32px; height: 32px; background: var(--teal); flex: none; }
  .card-front .brand-name { font-size: 19px; color: var(--ink); }
  .front-divider {
    position: absolute; left: 336px; top: 70px;
    width: 2px; height: 185px;
    background: linear-gradient(to bottom, transparent, var(--divider) 20%, var(--divider) 80%, transparent);
  }
  .contact-block { position: absolute; left: 364px; top: 71px; }
  .person-name {
    font-family: "Roboto Condensed", Arial, sans-serif;
    font-weight: 700; font-size: 21px; color: var(--teal); line-height: 1.1;
  }
  .person-title {
    font-family: "Roboto Condensed", Arial, sans-serif;
    font-size: 15px; color: var(--ink); margin-top: 3px;
  }
  .address {
    font-size: 14px; color: var(--grey-text); line-height: 19px; margin-top: 11px;
  }
  .contact-list { list-style: none; margin-top: 10px; }
  .contact-list li {
    display: flex; align-items: center; gap: 9px;
    font-size: 14px; color: var(--grey-text); line-height: 19px;
  }
  .contact-list svg { width: 13px; height: 13px; fill: var(--teal); flex: none; }
  .web-band {
    position: absolute; left: 0; top: 290px; width: 600px; height: 35px;
    border-top: 2px solid #2b3b3d;
    background: linear-gradient(to right, #17969a, var(--teal-light) 55%, #17969a);
    color: #ffffff; font-size: 13px; letter-spacing: 4px;
    display: flex; align-items: center; justify-content: center;
  }

  /* Back */
  .card-back { left: 311px; top: 472px; background: var(--card-black); }
  .card-back .brand { left: 140px; top: 112px; width: 330px; gap: 12px; }
  .card-back .brand-square { width: 40px; height: 40px; background: #ffffff; flex: none; }
  .card-back .brand-name { color: #ffffff; font-size: 26px; }
  .back-rule {
    position: absolute; left: 44px; top: 263px; width: 513px; height: 1px; background: #ffffff;
  }
  .cert-badge {
    position: absolute; left: 42px; top: 278px; width: 96px; height: 26px;
    background: #ffffff; border-radius: 2px;
  }
  .partner-badge {
    position: absolute; left: 469px; top: 278px; width: 91px; height: 30px;
    background: #ffffff; border-radius: 2px;
  }
</style>
</head>
<body>
  <section class="card card-front">
    <div class="brand">
      <span class="brand-square"></span>
      <span class="brand-name">Kestrel Machining</span>
    </div>
    <div class="front-divider"></div>
    <div class="contact-block">
      <h1 class="person-name">DANIEL REYES</h1>
      <p class="person-title">CEO/FOUNDER</p>
      <p class="address">214 Harbour Ridge Road<br>Kelowna, BC V1Y 3K8</p>
      <ul class="contact-list">
        <li>
          <svg viewBox="0 0 16 16" aria-hidden="true"><path d="M3.5 1l2.6 3-1.4 1.9c.9 2 2.4 3.5 4.4 4.4L11 8.9l3 2.6-1.6 2.7C6.8 14 2 9.2 1 3.2z"/></svg>
          250 555 0142
        </li>
        <li>
          <svg viewBox="0 0 16 16" aria-hidden="true"><path d="M4.5 0h7a1 1 0 0 1 1 1v14a1 1 0 0 1-1 1h-7a1 1 0 0 1-1-1V1a1 1 0 0 1 1-1zm.8 2v10h5.4V2zM8 12.7a.9.9 0 1 0 0 1.8.9.9 0 0 0 0-1.8z"/></svg>
          250 555 0187
        </li>
        <li>
          <svg viewBox="0 0 16 16" aria-hidden="true"><path d="M4 1h8v4H4zM1 6h14v7h-2v-3H3v3H1zm3 5h8v4H4z"/></svg>
          250 555 0163
        </li>
        <li>
          <svg viewBox="0 0 16 16" aria-hidden="true"><path d="M1 3h14v10H1zm1.5 1.3v.4L8 8.6l5.5-3.9v-.4z"/></svg>
          marla@kestrelmachining.ca
        </li>
      </ul>
    </div>
    <div class="web-band">www.kestrelmachining.ca</div>
  </section>

  <section class="card card-back">
    <div class="brand">
      <span class="brand-square"></span>
      <span class="brand-name">Kestrel Machining</span>
    </div>
    <div class="back-rule"></div>
    <div class="cert-badge" role="img" aria-label="Quality certification badge"></div>
    <div class="partner-badge" role="img" aria-label="Partner listing badge"></div>
  </section>
</body>
</html>
```